Freight broker online presence/customer portal track shipping

I sleek design showing what we do, broker freight. What we specialize in, chemicals and any freight where domestic or international. We want a home page, a customer portal button on front page that lets clients check on status of their freight (integrate with our transportation management system. Contact page,
COMPANIES THAT HAVE PALLETS TO MOVE.
https://www.tallowmerelogistics.com/
https://www.quivendale.com/
https://www.rkpellow.com/
3 page

```html
<!DOCTYPE html>
<html lang="en">
<head>
<meta charset="utf-8">
<title>Freight Broker — Home</title>
<link rel="stylesheet" href="https://fonts.googleapis.com/css2?family=Montserrat:wght@600;700&family=Roboto:wght@400;500;700&family=Lato:wght@400;700&display=swap">
<style>
:root{
  --green:#a6cd37;
  --blue:#3777b4;
  --teal:#33b9a6;
  --red:#ef4a50;
  --ink:#222326;
  --muted:#666;
  --footer:#1e1e1f;
  --footer-text:#a9a9a9;
  --white:#fff;
}
*{box-sizing:border-box;margin:0;padding:0}
html,body{width:1200px;height:2892px;overflow:hidden}
body{position:relative;background:var(--white);font-family:'Roboto',sans-serif;color:var(--ink)}
.abs{position:absolute}

/* Hero */
.hero{left:0;top:0;width:1200px;height:657px;
  background:linear-gradient(110deg,#5b5f5c 0%,#8a7a64 30%,#c9bfb2 52%,#3b4556 72%,#1f2733 100%)}
.brand{left:110px;top:36px;font-family:'Montserrat',sans-serif;font-weight:700;font-size:22px;color:var(--white);letter-spacing:.2px}
.nav{top:42px;display:flex;font-family:'Roboto',sans-serif;font-weight:700;font-size:14.5px;color:var(--white)}
.nav a{position:absolute;white-space:nowrap;color:var(--white);text-decoration:none}
.nav a.active{color:var(--green)}
.nav a.active::after{content:"";position:absolute;left:0;right:0;top:23px;height:2px;background:var(--green)}
.btn{display:flex;align-items:center;justify-content:center;border:2.5px solid var(--green);border-radius:24px;
  font-family:'Roboto',sans-serif;font-weight:700;font-size:14.5px;text-transform:uppercase;color:var(--ink);text-decoration:none}
.btn.light{color:var(--white)}
.btn.fill{background:var(--green);color:var(--white)}
.login{left:983px;top:30px;width:105px;height:43px}
.hero-panel{left:68px;top:257px;width:643px;height:189px;background:rgba(40,40,40,.55)}
.hero-title{left:108px;top:283px;font-family:'Montserrat',sans-serif;font-weight:700;font-size:55px;color:var(--white);letter-spacing:-.5px;white-space:nowrap}
.quote{left:108px;top:358px;width:182px;height:43px}
.portal{left:304px;top:358px;width:183px;height:43px}
.scroll-label{left:0;width:1200px;top:602px;text-align:center;font-size:14px;color:#2b2b2b}
.scroll-btn{left:574px;top:635px;width:52px;height:52px;border-radius:50%;background:var(--teal)}

/* Specialties */
.section-title{left:0;width:1200px;top:752px;text-align:center;font-family:'Montserrat',sans-serif;font-weight:700;font-size:36px;color:var(--ink)}
.card{top:828px;width:300px;text-align:center}
.card .icon{width:80px;height:84px;margin:0 auto;background:#e4eef8;border-radius:6px}
.card h3{margin-top:20px;font-family:'Montserrat',sans-serif;font-weight:700;font-size:22px;color:var(--ink)}
.card .rule{width:44px;height:3px;background:var(--green);margin:12px auto 0}
.card p{margin-top:17px;font-size:14.5px;line-height:21.5px;color:var(--muted)}
.card .btn{width:140px;height:43px;margin:14px auto 0}

/* Feature rows */
.band{width:600px;height:429px}
.photo{width:600px;height:429px}
.feature h2{font-family:'Montserrat',sans-serif;font-weight:700;font-size:37px;line-height:38px;color:var(--white)}
.feature p{margin-top:20px;width:430px;font-size:14.5px;line-height:21.4px;color:var(--white)}
.feature .btn{margin-top:28px;width:140px;height:43px;color:var(--white)}

/* Footer */
.footer{left:0;top:2496px;width:1200px;height:396px;background:var(--footer)}
.chat{left:1116px;top:2545px;width:54px;height:54px;border-radius:50%;background:var(--green)}
.f-col{top:2607px;font-family:'Lato',sans-serif}
.f-col h4{font-family:'Lato',sans-serif;font-weight:700;font-size:18px;color:var(--white)}
.f-col ul{list-style:none;margin-top:16px}
.f-col li{font-size:13.5px;line-height:22.5px;color:var(--footer-text)}
.f-col li::before{content:"»";margin-right:9px;color:var(--footer-text)}
.socials{display:flex;gap:5px;margin-top:22px}
.socials span{width:36px;height:36px;border-radius:50%;background:var(--white)}
.f-col .blurb{margin-top:16px;width:275px;font-size:13.5px;line-height:22.5px;color:var(--footer-text)}
.subscribe{margin-top:20px;width:273px;height:44px;background:#2c2c2d;display:flex;align-items:center;justify-content:space-between;padding:0 16px;font-size:13.5px;color:var(--footer-text)}
.f-rule{left:110px;top:2810px;width:978px;height:1px;background:#303031}
.copyright{left:0;width:1200px;top:2836px;text-align:center;font-family:'Lato',sans-serif;font-size:14px;color:var(--white)}
</style>
</head>
<body>

<!-- Hero -->
<div class="abs hero" role="img" aria-label="Photo of a business team working at a laptop in front of a container port, with a faint world route map overlay"></div>
<div class="abs brand">FREIGHT BROKER</div>
<nav class="abs nav" style="left:0;top:43px">
  <a class="active" href="#" style="left:513px">HOME</a>
  <a href="#" style="left:583px">CUSTOMERS</a>
  <a href="#" style="left:698px">SERVICES</a>
  <a href="#" style="left:794px">CAREERS</a>
  <a href="#" style="left:886px">CONTACT</a>
</nav>
<a class="abs btn light login" href="#">LOGIN</a>
<div class="abs hero-panel"></div>
<h1 class="abs hero-title">WE GOT IT COVERED</h1>
<a class="abs btn light quote" href="#">REQUEST A QUOTE</a>
<a class="abs btn fill portal" href="#">CUSTOMER PORTAL</a>
<div class="abs scroll-label">SCROLL DOWN</div>
<div class="abs scroll-btn">
  <svg width="52" height="52" viewBox="0 0 52 52" fill="none" stroke="#fff" stroke-width="2.2" stroke-linecap="round" stroke-linejoin="round">
    <path d="M26 16v20M18 28l8 8 8-8"/>
  </svg>
</div>

<!-- Specialties -->
<h2 class="abs section-title">WHAT WE SPECIALIZE IN</h2>
<div class="abs card" style="left:125px">
  <div class="icon" role="img" aria-label="Line icon of a group of customers"></div>
  <h3>CUSTOMERS</h3><div class="rule"></div>
  <p>Lorem ipsum dolor sit amet, consectetur adipiscing elit, sed do eiusmod tempor incididunt</p>
  <a class="btn" href="#">LEARN MORE</a>
</div>
<div class="abs card" style="left:450px">
  <div class="icon" role="img" aria-label="Line icon of a hand truck carrying boxes"></div>
  <h3>CARRIERS</h3><div class="rule"></div>
  <p>Lorem ipsum dolor sit amet, consectetur adipiscing elit, sed do eiusmod tempor incididunt</p>
  <a class="btn" href="#">LEARN MORE</a>
</div>
<div class="abs card" style="left:775px">
  <div class="icon" role="img" aria-label="Line icon of a climber planting a flag on top of steps"></div>
  <h3>CAREERS</h3><div class="rule"></div>
  <p>Lorem ipsum dolor sit amet, consectetur adipiscing elit, sed do eiusmod tempor incididunt</p>
  <a class="btn" href="#">LEARN MORE</a>
</div>

<!-- About -->
<div class="abs band" style="left:0;top:1212px;background:var(--blue)"></div>
<div class="abs feature" style="left:111px;top:1285px">
  <h2>ABOUT US</h2>
  <p>Lorem ipsum dolor sit amet, consectetur adipiscing elit, sed do eiusmod tempor incididunt ut labore et dolore magna aliqua. Ut enim ad minim veniam, quis nostrud exercitation ullamco laboris nisi ut aliquip ex ea commodo consequat. Duis aute irure dolor in reprehenderit in voluptate velit esse cillum dolore eu fugiat nulla pariatur. Excepteur sint occaecat cupidatat non proident, sunt in culpa qui officia deserunt mollit anim id est laborum.</p>
  <a class="btn" href="#">LEARN MORE</a>
</div>
<div class="abs photo" style="left:600px;top:1212px;background:linear-gradient(180deg,#5d95d4 0%,#b9d3ee 35%,#b24a3c 65%,#4a5563 100%)" role="img" aria-label="Photo of a container yard with a forklift lifting a red shipping container"></div>

<!-- Corporate -->
<div class="abs photo" style="left:0;top:1640px;background:linear-gradient(180deg,#3f78c6 0%,#86b3e2 35%,#2f6fa8 60%,#c44a6e 100%)" role="img" aria-label="Aerial photo of a loaded container ship beside gantry cranes at sea"></div>
<div class="abs band" style="left:600px;top:1640px;background:var(--teal)"></div>
<div class="abs feature" style="left:688px;top:1695px">
  <h2>CORPORATE<br>INFORMATION</h2>
  <p>Lorem ipsum dolor sit amet, consectetur adipiscing elit, sed do eiusmod tempor incididunt ut labore et dolore magna aliqua. Ut enim ad minim veniam, quis nostrud exercitation ullamco laboris nisi ut aliquip ex ea commodo consequat. Duis aute irure dolor in reprehenderit in voluptate velit esse cillum dolore eu fugiat nulla pariatur. Excepteur sint occaecat cupidatat non proident, sunt in culpa qui officia deserunt mollit anim id est laborum.</p>
  <a class="btn" href="#">LEARN MORE</a>
</div>

<!-- What we do -->
<div class="abs band" style="left:0;top:2069px;background:var(--red)"></div>
<div class="abs feature" style="left:88px;top:2141px">
  <h2>WHAT WE DO</h2>
  <p>Lorem ipsum dolor sit amet, consectetur adipiscing elit, sed do eiusmod tempor incididunt ut labore et dolore magna aliqua. Ut enim ad minim veniam, quis nostrud exercitation ullamco laboris nisi ut aliquip ex ea commodo consequat. Duis aute irure dolor in reprehenderit in voluptate velit esse cillum dolore eu fugiat nulla pariatur. Excepteur sint occaecat cupidatat non proident, sunt in culpa qui officia deserunt mollit anim id est laborum.</p>
  <a class="btn" href="#">LEARN MORE</a>
</div>
<div class="abs photo" style="left:600px;top:2069px;background:linear-gradient(135deg,#8c8478 0%,#c9c3b8 45%,#7b6f62 100%)" role="img" aria-label="Photo of a warehouse worker standing beside shelving and a forklift"></div>

<!-- Footer -->
<footer class="abs footer"></footer>
<div class="abs chat">
  <svg width="54" height="54" viewBox="0 0 54 54"><path d="M27 17c-7 0-12 4.3-12 9.5 0 2.8 1.4 5.2 3.7 6.9L17.5 38l5.3-2.6c1.3.4 2.7.6 4.2.6 7 0 12-4.3 12-9.5S34 17 27 17z" fill="#fff"/></svg>
</div>
<div class="abs f-col" style="left:110px">
  <h4>Follow us</h4>
  <div class="socials" aria-label="Social media links"><span></span><span></span><span></span><span></span></div>
</div>
<div class="abs f-col" style="left:351px">
  <h4>Company</h4>
  <ul><li>Our Story</li><li>Careers</li><li>Privacy Policy</li><li>Terms and Conditions</li></ul>
</div>
<div class="abs f-col" style="left:592px">
  <h4>Help</h4>
  <ul><li>Returns &amp; Exchanges</li><li>FAQ</li><li>Size Guide</li><li>Search</li></ul>
</div>
<div class="abs f-col" style="left:815px">
  <h4>Newsletter</h4>
  <p class="blurb">Lorem ipsum dolor sit amet, consectetur adipi scing elit, sed do eiusmod tempor</p>
  <div class="subscribe">
    <span>Email address</span>
    <svg width="16" height="16" viewBox="0 0 16 16"><path d="M15 1L1 7l5 2 2 6 7-14z" fill="var(--green)"/></svg>
  </div>
</div>
<div class="abs f-rule"></div>
<div class="abs copyright">© Copyrights Company name 2021. All rights reserved | Privacy policy | Terms Condition</div>

</body>
</html>
```